Looking for a modern, Professional business card design

We have a simple business card, but are looking for a more modern, professional look. A sample of the basic card is attached as well as the logo. We would also like to add that we offer:
Struggling with your finances?
- Learn to become debt free
- Discover the power of cash
- Control your money instead of it controlling you
Let us help you achieve a new level of financial freedom!
Also, we would like to have a "SPECIAL OFFER!: FREE 30 minute consultation"
Financial Planning

```html
<!DOCTYPE html>
<html lang="en">
<head>
<meta charset="utf-8">
<title>Steady Ledger Coaching – Business Card</title>
<link href="https://fonts.googleapis.com/css2?family=Arimo:wght@400;700&family=Archivo+Black&display=swap" rel="stylesheet">
<style>
  :root {
    --page-bg: #8c8c8c;
    --card-white: #ebebeb;
    --brand-green: #2f9a3e;
    --accent-green: #8cc63f;
    --deep-green: #2b8a37;
    --ink: #111111;
    --grey-text: #3c3c3c;
    --on-green: #ffffff;
  }
  * { margin: 0; padding: 0; box-sizing: border-box; }
  html, body { width: 1105px; height: 1200px; overflow: hidden; }
  body {
    background: var(--page-bg);
    font-family: "Arimo", Arial, sans-serif;
    position: relative;
  }
  .card {
    position: absolute;
    left: 182px;
    width: 709px;
    height: 427px;
    background: var(--card-white);
    overflow: hidden;
  }
  .card--front { top: 119px; }
  .card--back { top: 637px; }

  /* front */
  .front-shape { position: absolute; inset: 0; }
  .contact-block { position: absolute; left: 32px; top: 135px; color: var(--on-green); }
  .contact-name { font-size: 26px; font-weight: 400; letter-spacing: 0.5px; }
  .contact-role { font-size: 19px; margin-top: 6px; opacity: 0.95; }
  .contact-list { list-style: none; margin-top: 26px; }
  .contact-list li {
    display: flex; align-items: center; gap: 14px;
    font-size: 18px; height: 29px;
  }
  .contact-list svg { width: 18px; height: 18px; flex: none; }

  .brand {
    position: absolute;
    display: flex; align-items: center;
    font-family: "Arimo", Arial, sans-serif;
    font-weight: 700;
    color: var(--deep-green);
    white-space: nowrap;
  }
  .brand-name { display: flex; flex-direction: column; line-height: 1.1; }
  .brand-dot { border-radius: 50%; background: var(--accent-green); flex: none; }
  .brand--front { left: 462px; top: 158px; font-size: 23px; gap: 9px; }
  .brand--front .brand-dot { width: 22px; height: 22px; }
  .brand--back { left: 0; right: 0; justify-content: center; top: 52px; font-size: 48px; gap: 18px; }
  .brand--back .brand-dot { width: 46px; height: 46px; }

  /* back */
  .pitch { position: absolute; left: 0; right: 0; top: 238px; text-align: center; }
  .pitch-heading { color: var(--deep-green); font-size: 22px; font-weight: 400; letter-spacing: 0.3px; }
  .pitch-line { color: var(--grey-text); font-size: 20px; margin-top: 5px; }
  .pitch-bullet {
    display: inline-block; width: 7px; height: 7px; border-radius: 50%;
    background: var(--brand-green); vertical-align: middle; margin: 0 4px 3px;
  }
  .pitch-cta { color: var(--ink); font-size: 19px; font-weight: 700; margin-top: 5px; }
  .pitch-rule {
    width: 560px; height: 2px; background: var(--brand-green);
    margin: 8px auto 0;
  }
  .special-offer {
    font-family: "Archivo Black", "Arial Black", sans-serif;
    color: var(--brand-green);
    font-size: 25px; margin-top: 10px; letter-spacing: 0.3px;
  }
</style>
</head>
<body>

<section class="card card--front" aria-label="Card front">
  <svg class="front-shape" viewBox="0 0 709 427" preserveAspectRatio="none" aria-hidden="true">
    <path d="M0 0 H432 C395 120 380 300 446 427 H0 Z" fill="var(--brand-green)"/>
    <path d="M432 0 H450 C408 120 394 300 458 427 H446 C380 300 395 120 432 0 Z" fill="var(--accent-green)"/>
    <path d="M466 0 H472 C428 120 414 300 474 427 H469 C408 300 422 120 466 0 Z" fill="var(--ink)"/>
  </svg>

  <div class="contact-block">
    <h1 class="contact-name">DANIEL R. WHITAKER</h1>
    <p class="contact-role">Personal Financial Coach</p>
    <ul class="contact-list">
      <li>
        <svg viewBox="0 0 18 18"><rect x="4" y="1" width="10" height="16" rx="2" fill="none" stroke="currentColor" stroke-width="1.6"/><circle cx="9" cy="14" r="1" fill="currentColor"/></svg>
        (555) 010-2843
      </li>
      <li>
        <svg viewBox="0 0 18 18"><rect x="1" y="4" width="16" height="11" rx="1" fill="currentColor"/><path d="M1.5 4.5 L9 10.5 L16.5 4.5" fill="none" stroke="var(--brand-green)" stroke-width="1.4"/></svg>
        daniel@steadyledgerplanning.com
      </li>
      <li>
        <svg viewBox="0 0 18 18"><circle cx="9" cy="9" r="8" fill="currentColor"/><path d="M9 1 C5 5 5 13 9 17 M9 1 C13 5 13 13 9 17 M1 9 H17" fill="none" stroke="var(--brand-green)" stroke-width="1.2"/></svg>
        www.steadyledgerplanning.com
      </li>
    </ul>
  </div>

  <div class="brand brand--front">
    <span class="brand-dot"></span>
    <span class="brand-name"><span>STEADY LEDGER</span><span>COACHING</span></span>
  </div>
</section>

<section class="card card--back" aria-label="Card back">
  <div class="brand brand--back">
    <span class="brand-dot"></span>
    <span class="brand-name"><span>STEADY LEDGER</span><span>COACHING</span></span>
  </div>

  <div class="pitch">
    <h2 class="pitch-heading">STRUGGLING WITH YOUR FINANCES?</h2>
    <p class="pitch-line">Learn to become debt free<span class="pitch-bullet"></span>Discover the power of cash</p>
    <p class="pitch-line">Control your money instead of it controlling you</p>
    <p class="pitch-cta">Let us help you achieve a new level of financial freedom!</p>
    <div class="pitch-rule"></div>
    <p class="special-offer">SPECIAL OFFER!: FREE 30 minute consultation</p>
  </div>
</section>

</body>
</html>
```